Web App Design Project

Need to provide graphical design of 2 web pages according to attached wireframes.

Colors should be adjusted for the 65+ population meaning not too bright.

App logo should be created as well - logo should represent long and good life.

Target Market(s)

65 years old and above

```html
<!DOCTYPE html>
<html lang="en">
<head>
<meta charset="utf-8">
<title>AppName – Medications</title>
<link href="https://fonts.googleapis.com/css2?family=Arimo:wght@400;700&display=swap" rel="stylesheet">
<style>
  :root {
    --page-bg: #c9ced9;
    --header-top: #b3b8ca;
    --header-bottom: #858aa1;
    --header-text: #f2f3f8;
    --sidebar-bg: #f2f2f3;
    --sidebar-line: #dcdce2;
    --surface: #ffffff;
    --ink: #5c5f72;
    --ink-soft: #a6a8b8;
    --row-border: #cbccd9;
    --button-bg: #a9abbd;
    --nav-bg: #474a5e;
    --nav-active: #56596d;
    --nav-divider: #3a3d4f;
    --nav-text: #d6d8e3;
  }
  * { box-sizing: border-box; margin: 0; padding: 0; }
  html, body { width: 1200px; height: 900px; overflow: hidden; }
  body { background: var(--page-bg); font-family: "Arimo", Arial, sans-serif; color: var(--ink); position: relative; }

  .app-window { position: absolute; left: 100px; top: 120px; width: 1000px; height: 660px; background: var(--surface); box-shadow: 0 10px 40px rgba(40,45,70,.25); }

  .app-header { position: absolute; left: 0; top: 0; width: 1000px; height: 60px; background: linear-gradient(var(--header-top), var(--header-bottom)); color: var(--header-text); }
  .brand { position: absolute; left: 0; top: 0; width: 200px; height: 60px; border-right: 1px solid rgba(255,255,255,.25); display: flex; align-items: center; padding-left: 22px; gap: 12px; }
  .brand-mark { width: 36px; height: 36px; border-radius: 50%; background: #e8eaf2; }
  .brand-name { font-size: 19px; font-weight: 700; line-height: 18px; }
  .brand-slogan { font-size: 9px; line-height: 11px; }
  .welcome { position: absolute; left: 215px; top: 21px; font-size: 16px; }
  .welcome strong { color: #fff; }
  .text-size { position: absolute; left: 610px; top: 18px; display: flex; align-items: baseline; gap: 12px; font-weight: 700; }
  .text-size span:nth-child(1) { font-size: 11px; opacity: .6; }
  .text-size span:nth-child(2) { font-size: 17px; color: #fff; }
  .text-size span:nth-child(3) { font-size: 20px; font-weight: 400; opacity: .6; }
  .search { position: absolute; left: 686px; top: 14px; width: 163px; height: 31px; border: 1px solid rgba(255,255,255,.4); background: rgba(255,255,255,.08); padding: 7px 9px; font-size: 14px; color: #e3e5ee; }
  .search svg { position: absolute; right: 8px; top: 7px; }
  .header-btn { position: absolute; top: 14px; height: 31px; background: #8d92a7; border: 1px solid #a7abbd; color: #fff; font-weight: 700; font-size: 16px; text-align: center; line-height: 29px; }
  .btn-help { left: 888px; width: 32px; }
  .btn-exit { left: 934px; width: 52px; }

  .sidebar { position: absolute; left: 0; top: 60px; width: 200px; height: 470px; background: var(--sidebar-bg); border-right: 1px solid var(--sidebar-line); }
  .sidebar-title { text-align: center; font-size: 20px; font-weight: 700; margin-top: 23px; }
  .period { position: absolute; left: 10px; width: 190px; height: 90px; display: flex; align-items: center; gap: 10px; padding-left: 28px; font-size: 16px; font-weight: 700; color: var(--ink-soft); }
  .period.is-active { background: var(--surface); width: 191px; box-shadow: 0 1px 3px rgba(0,0,0,.08); }

  .toolbar-add { position: absolute; left: 216px; top: 82px; display: flex; align-items: center; gap: 6px; font-size: 16px; font-weight: 700; color: var(--ink-soft); }
  .toolbar-settings { position: absolute; left: 959px; top: 82px; }

  .med-row { position: absolute; left: 230px; width: 741px; height: 61px; border: 1px solid var(--row-border); border-radius: 3px; }
  .mark-taken { position: absolute; left: 14px; top: 15px; width: 100px; height: 30px; background: var(--button-bg); color: #fff; font-size: 13px; font-weight: 700; line-height: 30px; text-align: center; border-radius: 2px; }
  .med-name { position: absolute; left: 147px; top: 21px; font-size: 16px; }
  .med-dose { position: absolute; left: 576px; top: 21px; font-size: 16px; font-weight: 700; }
  .med-form { position: absolute; left: 608px; top: 18px; }
  .med-info { position: absolute; left: 700px; top: 21px; }

  .main-nav { position: absolute; left: 0; top: 530px; width: 1000px; height: 130px; background: var(--nav-bg); display: flex; }
  .nav-item { flex: 1; border-right: 1px solid var(--nav-divider); display: flex; flex-direction: column; align-items: center; padding-top: 30px; color: var(--nav-text); font-size: 14px; font-weight: 700; text-align: center; line-height: 17px; }
  .nav-item:last-child { border-right: 0; }
  .nav-item.is-active { background: var(--nav-active); color: #fff; }
  .nav-label { height: 36px; display: flex; align-items: center; margin-top: 17px; }
</style>
</head>
<body>
<svg width="0" height="0" style="position:absolute">
  <defs>
    <g id="atom" fill="none" stroke="currentColor" stroke-width="1.6">
      <ellipse cx="16" cy="16" rx="14" ry="5.5"/>
      <ellipse cx="16" cy="16" rx="14" ry="5.5" transform="rotate(60 16 16)"/>
      <ellipse cx="16" cy="16" rx="14" ry="5.5" transform="rotate(-60 16 16)"/>
      <circle cx="16" cy="16" r="2.2" fill="currentColor"/>
    </g>
    <g id="info" fill="none" stroke="#a6a8b8" stroke-width="1.2">
      <circle cx="9" cy="9" r="8.5"/>
      <line x1="9" y1="8" x2="8" y2="13"/>
      <circle cx="9.5" cy="5.3" r=".6" fill="#a6a8b8"/>
    </g>
  </defs>
</svg>

<main class="app-window">
  <header class="app-header">
    <div class="brand">
      <span class="brand-mark"></span>
      <div>
        <div class="brand-name">AppName</div>
        <div class="brand-slogan">Here is your slogan</div>
      </div>
    </div>
    <div class="welcome">Welcome back, <strong>Walter Grey</strong></div>
    <div class="text-size"><span>A</span><span>A</span><span>A</span></div>
    <div class="search">Search
      <svg width="16" height="16" viewBox="0 0 16 16" fill="none" stroke="#e3e5ee" stroke-width="2"><circle cx="6.5" cy="6.5" r="5"/><line x1="10" y1="10" x2="15" y2="15"/></svg>
    </div>
    <div class="header-btn btn-help">?</div>
    <div class="header-btn btn-exit">Exit</div>
  </header>

  <aside class="sidebar">
    <h2 class="sidebar-title">Medications</h2>
    <div class="period is-active" style="top:70px">
      <svg width="34" height="32" viewBox="0 0 34 32" fill="none" stroke="#a6a8b8" stroke-width="1.5"><path d="M9 14a8 8 0 0 1 16 0"/><line x1="17" y1="1" x2="17" y2="4"/><line x1="7" y1="5" x2="9" y2="7"/><line x1="27" y1="5" x2="25" y2="7"/><line x1="2" y1="12" x2="5" y2="12"/><line x1="29" y1="12" x2="32" y2="12"/><line x1="2" y1="17" x2="32" y2="17"/><line x1="2" y1="22" x2="32" y2="22"/><line x1="2" y1="27" x2="32" y2="27"/></svg>
      Morning
    </div>
    <div class="period" style="top:170px">
      <svg width="34" height="32" viewBox="0 0 34 32" fill="none" stroke="#a6a8b8" stroke-width="1.5"><circle cx="17" cy="16" r="7"/><line x1="17" y1="2" x2="17" y2="6"/><line x1="17" y1="26" x2="17" y2="30"/><line x1="3" y1="16" x2="7" y2="16"/><line x1="27" y1="16" x2="31" y2="16"/><line x1="7" y1="6" x2="10" y2="9"/><line x1="27" y1="6" x2="24" y2="9"/><line x1="7" y1="26" x2="10" y2="23"/><line x1="27" y1="26" x2="24" y2="23"/></svg>
      Noon
    </div>
    <div class="period" style="top:270px">
      <svg width="34" height="34" viewBox="0 0 34 34" fill="none" stroke="#a6a8b8" stroke-width="1.5"><path d="M8 15a7 7 0 0 1 13-4"/><line x1="14" y1="2" x2="14" y2="5"/><line x1="5" y1="7" x2="7" y2="9"/><line x1="2" y1="15" x2="5" y2="15"/><path d="M7 31a5 5 0 0 1 0-10a7 7 0 0 1 13-2a6 6 0 0 1 7 6a4 4 0 0 1 0 6z"/></svg>
      Afternoon
    </div>
    <div class="period" style="top:370px">
      <svg width="34" height="34" viewBox="0 0 34 34" fill="none" stroke="#a6a8b8" stroke-width="1.5"><path d="M16 3a14 14 0 1 0 15 18A12 12 0 0 1 16 3z"/></svg>
      Night
    </div>
  </aside>

  <div class="toolbar-add">
    <svg width="25" height="25" viewBox="0 0 25 25" fill="none" stroke="#a6a8b8" stroke-width="1.6"><circle cx="12.5" cy="12.5" r="11.5"/><line x1="12.5" y1="6" x2="12.5" y2="19"/><line x1="6" y1="12.5" x2="19" y2="12.5"/></svg>
    Add medication
  </div>
  <svg class="toolbar-settings" width="26" height="26" viewBox="0 0 26 26" fill="none" stroke="#a6a8b8" stroke-width="1.6"><circle cx="13" cy="13" r="12"/><circle cx="13" cy="13" r="6.5" stroke-dasharray="2.5 1.6" stroke-width="3"/><circle cx="13" cy="13" r="2.5"/></svg>

  <section class="med-row" style="top:145px">
    <div class="mark-taken">Mark as taken</div>
    <div class="med-name">Veldora (indomethacin)</div>
    <div class="med-dose">4x</div>
    <svg class="med-form" width="24" height="24" viewBox="0 0 24 24" fill="none" stroke="#5c5f72" stroke-width="1.4"><rect x="2" y="8" width="20" height="8" rx="4" transform="rotate(-45 12 12)"/><line x1="9" y1="9" x2="15" y2="15"/></svg>
    <svg class="med-info" width="18" height="18"><use href="#info"/></svg>
  </section>

  <section class="med-row" style="top:245px">
    <div class="mark-taken">Mark as taken</div>
    <div class="med-name">Coraxin (dabigatran)</div>
    <div class="med-dose">2x</div>
    <svg class="med-form" width="24" height="24" viewBox="0 0 24 24" fill="none" stroke="#5c5f72" stroke-width="1.4"><rect x="3" y="6" width="12" height="16" rx="2"/><rect x="5" y="2" width="8" height="4"/><line x1="5" y1="12" x2="13" y2="12"/><line x1="19" y1="8" x2="19" y2="20"/><ellipse cx="19" cy="6" rx="2" ry="3"/></svg>
    <svg class="med-info" width="18" height="18"><use href="#info"/></svg>
  </section>

  <section class="med-row" style="top:345px">
    <div class="mark-taken">Mark as taken</div>
    <div class="med-name">Gastrelin (omeprazole)</div>
    <div class="med-dose">1x</div>
    <svg class="med-form" width="24" height="24" viewBox="0 0 24 24" fill="none" stroke="#5c5f72" stroke-width="1.4"><rect x="6" y="7" width="7" height="14" transform="rotate(45 12 12)"/><line x1="16" y1="8" x2="20" y2="4"/><line x1="18" y1="2" x2="22" y2="6"/><line x1="3" y1="21" x2="6" y2="18"/></svg>
    <svg class="med-info" width="18" height="18"><use href="#info"/></svg>
  </section>

  <nav class="main-nav">
    <div class="nav-item is-active"><svg width="32" height="32"><use href="#atom"/></svg><span class="nav-label">Medications</span></div>
    <div class="nav-item"><svg width="32" height="32"><use href="#atom"/></svg><span class="nav-label">Home<br>Measurements</span></div>
    <div class="nav-item"><svg width="32" height="32"><use href="#atom"/></svg><span class="nav-label">My Schedule</span></div>
    <div class="nav-item"><svg width="32" height="32"><use href="#atom"/></svg><span class="nav-label">Lab Test Results</span></div>
    <div class="nav-item"><svg width="32" height="32"><use href="#atom"/></svg><span class="nav-label">Checkups &amp;<br>Procedures</span></div>
    <div class="nav-item"><svg width="32" height="32"><use href="#atom"/></svg><span class="nav-label">My Profile</span></div>
    <div class="nav-item"><svg width="32" height="32"><use href="#atom"/></svg><span class="nav-label">My Health Care<br>Providers</span></div>
  </nav>
</main>
</body>
</html>
```